Business cards to launch an education platform

Hi,
I am looking at having new business cards designed.
I am a startup, developing a web platform for schools and university, the education world. It's an online assessment system.
I would like a card that looks classy, and that is using the colors and the font of my logo.

I have attached:
1) my logo
2) A business card that I have designed quickly so you can have all the information required in the card, but I really don't like it.
3) The font that I am using (Lato Regular) to design my web platform
4) Some screenshots of my web platform so you can have a look at the style that I have.

Target Market(s)

Major market: Education system: Schools and university
Minor markets: Business in general

Industry/Entity Type

Business

Contact Information for Business Card

Clara Fenwick
Director

M: 0437 518 902
E: clara.fenwick@amberLoomSystems.com.au

Requirements
Must have
• The colors of my logo

```html
<!DOCTYPE html>
<html lang="en">
<head>
<meta charset="utf-8">
<title>Amber Loom Systems – Business Cards</title>
<link href="https://fonts.googleapis.com/css2?family=Lato:wght@400;700&display=swap" rel="stylesheet">
<style>
  :root {
    --sky: #29abe2;
    --navy: #1b4f8a;
    --ink: #1d4e89;
    --grey-text: #4a4a4a;
    --paper: #ffffff;
    --backdrop: #e9ecef;
  }
  * { box-sizing: border-box; margin: 0; padding: 0; }
  html, body {
    width: 1200px;
    height: 950px;
    overflow: hidden;
    background: var(--backdrop);
    font-family: "Lato", Arial, sans-serif;
  }
  .canvas {
    position: relative;
    width: 1200px;
    height: 950px;
  }
  .card {
    position: absolute;
    left: 250px;
    width: 700px;
    height: 400px;
    overflow: hidden;
    box-shadow: 0 6px 18px rgba(0,0,0,0.18);
  }
  /* Back side */
  .card--back {
    top: 50px;
    background: var(--sky);
    color: var(--paper);
  }
  .back-brand {
    position: absolute;
    top: 140px;
    left: 0;
    width: 100%;
    display: flex;
    align-items: center;
    justify-content: center;
    gap: 18px;
  }
  .brand-square {
    width: 62px;
    height: 62px;
    background: var(--paper);
  }
  .brand-name {
    font-size: 42px;
    font-weight: 400;
    letter-spacing: 2px;
  }
  .card--back .brand-name { color: var(--paper); }
  .back-web {
    position: absolute;
    bottom: 62px;
    width: 100%;
    text-align: center;
    font-size: 17px;
    letter-spacing: 0.5px;
  }
  /* Front side */
  .card--front {
    top: 500px;
    background: var(--paper);
  }
  .front-shapes {
    position: absolute;
    inset: 0;
  }
  .front-brand {
    position: absolute;
    top: 48px;
    right: 60px;
    display: flex;
    align-items: center;
    gap: 12px;
  }
  .front-brand .brand-square {
    width: 40px;
    height: 40px;
    background: var(--sky);
  }
  .front-brand .brand-name {
    font-size: 28px;
    color: var(--ink);
    letter-spacing: 1.5px;
  }
  .holder {
    position: absolute;
    left: 60px;
    top: 238px;
  }
  .holder-name {
    font-size: 24px;
    font-weight: 700;
    color: var(--ink);
  }
  .holder-role {
    margin-top: 4px;
    font-size: 17px;
    color: var(--sky);
  }
  .contacts {
    position: absolute;
    left: 60px;
    top: 318px;
    list-style: none;
  }
  .contacts li {
    display: flex;
    align-items: center;
    gap: 12px;
    font-size: 17px;
    color: var(--grey-text);
    line-height: 28px;
  }
  .contacts svg { width: 16px; height: 16px; flex: none; }
</style>
</head>
<body>
<main class="canvas">

  <section class="card card--back" aria-label="Card back">
    <div class="back-brand">
      <span class="brand-square"></span>
      <span class="brand-name">AMBER LOOM SYSTEMS</span>
    </div>
    <p class="back-web">www.amberLoomSystems.com.au</p>
  </section>

  <section class="card card--front" aria-label="Card front">
    <svg class="front-shapes" viewBox="0 0 700 400" preserveAspectRatio="none" aria-hidden="true">
      <polygon points="0,0 70,0 0,150" fill="var(--navy)"/>
      <polygon points="700,120 700,270 640,270" fill="var(--sky)"/>
    </svg>

    <div class="front-brand">
      <span class="brand-square"></span>
      <span class="brand-name">AMBER LOOM SYSTEMS</span>
    </div>

    <div class="holder">
      <p class="holder-name">Clara Fenwick</p>
      <p class="holder-role">Director</p>
    </div>

    <ul class="contacts">
      <li>
        <svg viewBox="0 0 16 16" aria-hidden="true"><rect x="4" y="1" width="8" height="14" rx="1.5" fill="none" stroke="var(--ink)" stroke-width="1.6"/><circle cx="8" cy="12.5" r="0.9" fill="var(--ink)"/></svg>
        0437 518 902
      </li>
      <li>
        <svg viewBox="0 0 16 16" aria-hidden="true"><rect x="1" y="3" width="14" height="10" rx="1" fill="var(--ink)"/><polyline points="1.5,3.5 8,9 14.5,3.5" fill="none" stroke="#fff" stroke-width="1.3"/></svg>
        clara.fenwick@amberLoomSystems.com.au
      </li>
    </ul>
  </section>

</main>
</body>
</html>
```